Redesign of an existing homepage

This site needs a redesign
https://www.wanderhof-kelbach.de
This page with the accommodation options is important for the customer
https://www.wanderhof-kelbach.de/gastgeber/
Till now there is a new logo. See attachment. That's all I have.
It would make sense to use the colors of the logo in the redesign.
footer.jpg.
I would put this info into the footer. The graphic (Infomaterial) is not needed.
a new menu - links.jpg
This info can be put in a new menu. Therefore the right column is gone and there is more space for the design.
NEW:
Please keep in mind that the Icons are important and shall be displayed under every accommodation

```html
<!DOCTYPE html>
<html lang="de">
<head>
<meta charset="utf-8">
<title>Wanderhof Kelbach – Urlaub im Kelbachtal</title>
<link href="https://fonts.googleapis.com/css2?family=Quicksand:wght@500;600;700&family=Roboto+Condensed:wght@700&display=swap" rel="stylesheet">
<style>
:root{
  --blue:#0b5aa6;
  --green:#7cbb26;
  --lime:#c8d400;
  --grey:#7a7a7a;
  --text:#2b2b2b;
  --light:#f4f4f4;
  --black:#0d0d0d;
}
*{margin:0;padding:0;box-sizing:border-box}
html,body{width:1200px;height:3499px;overflow:hidden}
body{font-family:"Quicksand",sans-serif;color:var(--text);background:#fff;position:relative}
.abs{position:absolute}
/* header */
.header{position:absolute;left:0;top:0;width:1200px;height:108px;background:#fff;border-top:3px solid var(--green)}
.topbar{position:absolute;right:0;top:0;width:465px;height:47px;background:var(--green);clip-path:polygon(0 0,100% 0,100% 100%,30px 100%)}
.top-phone{position:absolute;left:772px;top:12px;color:#fff;font-weight:700;font-size:17px;display:flex;align-items:center;gap:8px}
.top-cta{position:absolute;left:960px;top:8px;width:99px;height:32px;background:var(--blue);color:#fff;font-weight:700;font-size:15px;text-align:center;line-height:32px}
.brand{position:absolute;left:142px;top:22px;display:flex;align-items:center;gap:10px;color:var(--blue);font-weight:700;font-size:17px;letter-spacing:.5px}
.brand .dot{width:34px;height:34px;border-radius:50%;background:var(--green)}
.brand small{display:block;font-size:11px;color:var(--grey);letter-spacing:1.5px;font-weight:600}
.nav{position:absolute;left:480px;top:68px;display:flex;gap:20px;font-size:12.5px;font-weight:600}
.nav a{color:var(--text);text-decoration:none}
.nav a.active{color:var(--blue)}
/* hero */
.hero{position:absolute;left:0;top:108px;width:1200px;height:524px;background:linear-gradient(180deg,#4f6a3a 0%,#7a9a4a 35%,#5c7348 60%,#3d4c40 100%)}
.hero h1{position:absolute;left:143px;top:175px;font-family:"Roboto Condensed",sans-serif;font-size:58px;color:#fff;line-height:1}
.hero p{position:absolute;left:143px;top:250px;font-size:27px;font-weight:700;color:#fff}
.hero .cta{position:absolute;left:142px;top:299px;width:130px;height:40px;background:var(--blue);color:#fff;font-weight:700;font-size:20px;text-align:center;line-height:40px}
/* headings */
.sec-title{position:absolute;left:0;width:1200px;text-align:center;font-size:33px;font-weight:700;color:var(--grey)}
.sec-title b{color:var(--blue)}
.sec-title::after{content:"";display:block;width:54px;height:3px;background:var(--grey);margin:10px auto 0}
/* intro */
.photo-frame{position:absolute;box-shadow:-7px 7px 0 var(--lime)}
.intro-text{position:absolute;left:560px;top:790px;width:505px;font-size:11.7px;line-height:22.5px;font-weight:600}
.intro-text p{margin-bottom:5px}
.intro-text .lead{color:var(--green);font-size:14px;margin-bottom:6px}
.intro-text .sign{color:var(--green);font-size:14px;margin-top:20px}
/* video */
.band-grey{position:absolute;left:0;width:1200px;background:var(--light)}
.video{position:absolute;left:183px;top:1420px;width:827px;height:425px;background:#fff;border-radius:12px;box-shadow:0 22px 24px -14px rgba(0,0,0,.35)}
.video .screen{position:absolute;left:8px;top:8px;width:811px;height:407px;border-radius:8px;background:linear-gradient(180deg,#a9c9e6 0%,#c8d9e2 18%,#6c7e60 30%,#8a8a80 60%,#5f6f55 100%)}
.video .bar{position:absolute;left:20px;right:20px;bottom:18px;height:3px;background:rgba(255,255,255,.6)}
/* stays */
.stays h2{position:absolute;left:142px;top:2108px;width:520px;font-size:27px;line-height:35px;color:var(--blue);font-weight:700}
.stays p{position:absolute;left:142px;width:490px;font-size:14px;line-height:25px;font-weight:600}
.stays .cta{position:absolute;left:142px;top:2301px;width:98px;height:31px;background:var(--blue);color:#fff;font-size:15px;font-weight:700;text-align:center;line-height:31px}
/* map */
.map{position:absolute;left:213px;top:2580px;width:573px;height:374px;border:4px solid var(--green);background:linear-gradient(135deg,#eef0ee,#e3e6e4)}
.loc{position:absolute;left:836px;top:2690px;font-weight:600}
.loc h3{font-size:33px;color:var(--blue);font-weight:700}
.loc h3::after{content:"";display:block;width:54px;height:3px;background:var(--blue);margin-top:8px}
.loc h4{font-size:16px;color:var(--grey);margin:18px 0 10px}
.loc p{font-size:12px;line-height:22px}
.partners{position:absolute;top:2990px;height:90px;background:#cfd7dc}
/* footer */
.footer{position:absolute;left:0;top:3157px;width:1200px;height:342px;background:var(--black);color:#fff}
.footer h5{font-size:15px;color:var(--lime);font-weight:700}
.footer h5::after{content:"";display:block;width:34px;height:2px;background:var(--lime);margin-top:5px}
.footer ul{list-style:none;font-size:12px;font-weight:600;line-height:25.5px;margin-top:6px}
.fcol-left{position:absolute;left:142px;top:80px}
.fcol-right{position:absolute;left:901px;top:80px}
.fbrand{position:absolute;left:420px;top:90px;width:360px;text-align:center;font-size:20px;font-weight:700;color:var(--green);letter-spacing:1px}
.fbrand small{display:block;font-size:14px;color:#fff;letter-spacing:2px;margin-top:4px}
.fcontact{position:absolute;left:390px;top:218px;display:flex;gap:28px;font-size:15px;font-weight:700}
.fcontact span{display:flex;align-items:center;gap:10px}
.fbottom{position:absolute;left:140px;top:294px;width:915px;border-top:1px solid #333;padding-top:14px;font-size:10.5px;font-weight:600;display:flex;justify-content:space-between}
.fbottom nav{display:flex;gap:18px}
</style>
</head>
<body>

<header class="header">
  <div class="topbar"></div>
  <div class="top-phone">
    <svg width="22" height="22" viewBox="0 0 24 24" fill="none" stroke="#fff" stroke-width="1.8"><path d="M5 3h4l2 5-2.5 1.5a11 11 0 0 0 6 6L16 13l5 2v4a2 2 0 0 1-2 2A17 17 0 0 1 3 5a2 2 0 0 1 2-2z"/><path d="M15 3a6 6 0 0 1 6 6M15 6.5a2.5 2.5 0 0 1 2.5 2.5"/></svg>
    0123 / 456 7890
  </div>
  <div class="top-cta">Kontakt</div>
  <div class="brand"><span class="dot"></span><div>GÄSTEVEREIN<small>KELBACH UND UMGEBUNG</small></div></div>
  <nav class="nav">
    <a class="active" href="https://www.wanderhof-kelbach.de">Heim</a>
    <a href="#">Kelbach</a>
    <a href="https://www.wanderhof-kelbach.de/gastgeber/">Gastgeber</a>
    <a href="#">Kelbachtal_Inn</a>
    <a href="#">Quellenland</a>
    <a href="#">Tourismusverband Waldhügelland</a>
  </nav>
</header>

<section class="hero" role="img" aria-label="Paar sitzt auf einem Steg am See und spritzt mit den Füßen ins Wasser, Bäume im Hintergrund">
  <h1>Waldhügelland Erleben</h1>
  <p>Noch Mehr Erleben In Waldhügelland</p>
  <div class="cta">Kontakt</div>
</section>

<h2 class="sec-title" style="top:710px"><b>Urlaub Im Kelbachtal –</b> Dem Schönsten Fleck Bayerns</h2>
<div class="photo-frame" role="img" aria-label="Luftbild eines Bauernhofs mit roten Dächern vor bewaldeten Hügeln" style="left:148px;top:791px;width:387px;height:366px;background:linear-gradient(180deg,#4d6a3c 0%,#6f8f4a 40%,#4f7a35 65%,#6b8d3e 100%)"></div>
<div class="intro-text">
  <p class="lead">Lieber Besucherinnen und Besucher</p>
  <p>Kelbach und Umgebung haben all das, was das Leben lebenswert macht: Kultur und Natur, Lebensfreude und Genuss, freundliche &amp; aufgeschlossene Mensche.</p>
  <p>Ob Kirchen, Brunnen oder andere Baudenkmäler – bei einem Rundgang durch die Kelbacher Ross-Stadt kann man viele liebevolle Details für sich entdecken.</p>
  <p>Für Bewegungsfreudige und Erholungssuchende gibt es "Natur pur" in und um Kelbach! Hier kann man sportlich unterwegs sein beim Radeln, Walken, Wandern, Golfen, Reiten und Baden oder einfach nur die Ruhe genießen</p>
  <p>Freizeit und Erholung für die ganze Familie – planen Sie einen Urlaub auf dem Bauernhof, in einer Ferienwohnung oder im Hotel. Ihr Urlaub im Kelbachtal wird ein einmaliges Erlebnis!</p>
  <p>Genießen Sie unsere Gastfreundschaft – ein Besuch lohnt sich zu jeder Jahreszeit.</p>
  <p>Wir freuen uns auf Sie!</p>
  <p class="sign">Ihr… Gästeverein Kelbach und Umgebung e. V.</p>
</div>

<div class="band-grey" style="top:1247px;height:699px"></div>
<h2 class="sec-title" style="top:1327px"><b>Video</b> Ansehen</h2>
<div class="video">
  <div class="screen" role="img" aria-label="Videovorschau: Luftaufnahme der Kleinstadt Kelbach">
    <svg class="abs" style="left:373px;top:180px" width="64" height="44" viewBox="0 0 64 44"><rect x="2" y="2" width="60" height="40" rx="8" fill="none" stroke="#fff" stroke-width="3"/><path d="M26 13l14 9-14 9z" fill="#fff"/></svg>
    <div class="bar"></div>
  </div>
</div>

<section class="stays">
  <h2>Finde mehr als 7.700.000 Unterkünfte weltweit von Gastgebern auf Holibo.</h2>
  <p style="top:2180px">Sichere Buchung und flexible Stornierungsmöglichkeiten. Jetzt Urlaub sorgenfrei planen! Super Locations.</p>
  <p style="top:2235px">Freizeit und Erholung für die ganze Familie – planen Sie einen Urlaub auf dem Bauernhof, in einer Ferienwohnung oder im Hotel</p>
  <div class="cta">Kontakt</div>
  <div class="photo-frame" role="img" aria-label="Beleuchteter Innenhof eines Hotels mit Arkaden am Abend" style="left:668px;top:2037px;width:387px;height:366px;box-shadow:7px 7px 0 var(--lime);background:linear-gradient(180deg,#6b5a4a 0%,#b98a4a 40%,#8a5a32 70%,#3a2a20 100%)"></div>
</section>

<div class="band-grey" style="top:2495px;height:662px"></div>
<div class="map" role="img" aria-label="Stadtplan von Kelbach mit Markierung des Gästevereins">
  <svg class="abs" style="left:248px;top:140px" width="22" height="30" viewBox="0 0 22 30"><path d="M11 29S1 17 1 11a10 10 0 0 1 20 0c0 6-10 18-10 18z" fill="#e53935"/><circle cx="11" cy="11" r="4" fill="#a4161a"/></svg>
</div>
<div class="loc">
  <h3>Lageplan</h3>
  <h4>Öffnungszeiten</h4>
  <p>Mo-Do&nbsp;&nbsp;&nbsp; 9:00 – 16:00 Uhr<br>Fr&nbsp;&nbsp;&nbsp;&nbsp;&nbsp; 9:00 – 12:30 Uhr</p>
  <p style="margin-top:4px">Marktplatz 5<br>12345 Kelbach</p>
</div>
<div class="partners" style="left:188px;width:130px;background:#e9b23a"></div>
<div class="partners" style="left:380px;width:170px;border-radius:45px;background:#cfe2f2"></div>
<div class="partners" style="left:614px;width:255px;background:#dfe6dc"></div>
<div class="partners" style="left:930px;width:80px;border-radius:50%;background:#8ccbe0"></div>

<footer class="footer">
  <div class="fcol-left">
    <h5>Schnelle Links</h5>
    <ul><li>Heim</li><li>Kelbach</li><li>Gastgeber</li><li>Kelbachtal_Inn</li><li>Quellenland</li><li>Tourismusverband Waldhügelland</li></ul>
  </div>
  <div class="fbrand">GÄSTEVEREIN<small>KELBACH UND UMGEBUNG</small></div>
  <div class="fcontact">
    <span><svg width="20" height="20" viewBox="0 0 24 24" fill="none" stroke="var(--green)" stroke-width="1.8"><path d="M5 3h4l2 5-2.5 1.5a11 11 0 0 0 6 6L16 13l5 2v4a2 2 0 0 1-2 2A17 17 0 0 1 3 5a2 2 0 0 1 2-2z"/></svg>Tel.: 0123 / 456 7890</span>
    <span><svg width="20" height="20" viewBox="0 0 24 24" fill="none" stroke="var(--green)" stroke-width="1.8"><path d="M5 3h4l2 5-2.5 1.5a11 11 0 0 0 6 6L16 13l5 2v4a2 2 0 0 1-2 2A17 17 0 0 1 3 5a2 2 0 0 1 2-2z"/></svg>Fax: 0123 / 456 7899</span>
  </div>
  <div class="fcol-right">
    <h5>Das Kelbachtal Entdecken</h5>
    <ul><li>Parish churches</li><li>Lindenmünster</li><li>Eichenfelden</li><li>Bad Birkenau</li><li>Bad Kieselbach</li><li>Schönwald &amp; Mossing</li></ul>
  </div>
  <div class="fbottom">
    <span>© 2025. Wanderhof-Kelbach. Alle Rechte Vorbehalten</span>
    <nav><span>Informationsmaterial</span><span>Impressum</span><span>Datenschutz</span></nav>
  </div>
</footer>

</body>
</html>
```